I need a business card design for my vidloomer channel called The Tidy Skillet Show. I make vidloomer cooking tutorials. I'd like the phrase " I'll see you next time, for my next meal" somewhere on the BC. The Vidloomer web address is www.vidloomer.example/user/TidySkilletShow
email - bookings@harrowlanemedia.example

Target Market(s)

This is for companies & business opportunities so it needs to look professional & sleek.

Industry/Entity Type

Cooking

Requirements
Must have
• Must have my Tidy skillet show logo on the card preferably top left. My name ( Marcus Delroy ). Name of my channel "Tidy Skillet Show" & the vidlomer logo & web address for my channel & the email bookings@harrowlanemedia.example & the 3 pics of food.

```html
<!DOCTYPE html>
<html lang="en">
<head>
<meta charset="utf-8">
<title>Tidy Skillet Show – Business Card</title>
<link rel="stylesheet" href="https://fonts.googleapis.com/css2?family=Roboto+Condensed:wght@700&display=swap">
<style>
  :root {
    --page-bg: #e9e4dc;
    --gold-light: #f6c845;
    --gold-mid: #e3a21e;
    --gold-deep: #a4600f;
    --brown-edge: #4a2a0c;
    --ink: #2a1a0c;
    --black: #0c0a08;
    --white: #ffffff;
    --frame-gold: #f0b326;
  }
  html, body {
    margin: 0;
    width: 1200px;
    height: 1000px;
    overflow: hidden;
    background: var(--page-bg);
    font-family: "Roboto Condensed", "Arial Narrow", sans-serif;
    font-weight: 700;
  }
  .card {
    position: absolute;
    left: 75px;
    top: 200px;
    width: 1050px;
    height: 600px;
    overflow: hidden;
    background:
      radial-gradient(ellipse 70% 80% at 55% 50%, var(--gold-light) 0%, var(--gold-mid) 45%, var(--gold-deep) 80%, var(--brown-edge) 100%);
    box-shadow: 0 6px 20px rgba(0,0,0,.25);
  }
  .card p, .card h1 { font-weight: 700; }
  .slogan-pill {
    position: absolute;
    left: 150px;
    top: 95px;
    width: 540px;
    height: 210px;
    background: var(--black);
    border: 3px solid var(--frame-gold);
    border-radius: 105px;
    box-sizing: border-box;
  }
  .slogan {
    position: absolute;
    left: 300px;
    top: 127px;
    width: 360px;
    margin: 0;
    color: var(--white);
    font-size: 40px;
    line-height: 48px;
    text-transform: uppercase;
    letter-spacing: 1px;
  }
  .channel-logo {
    position: absolute;
    left: 28px;
    top: 78px;
    width: 244px;
    height: 244px;
    border-radius: 50%;
    background: var(--black);
    border: 4px solid var(--frame-gold);
    box-sizing: border-box;
    display: flex;
    align-items: center;
    justify-content: center;
    text-align: center;
    color: var(--gold-light);
    font-size: 30px;
    line-height: 34px;
    text-transform: uppercase;
  }
  .food-photo {
    position: absolute;
    right: -4px;
    width: 215px;
    height: 196px;
    border: 4px solid var(--frame-gold);
    border-radius: 98px 0 0 98px;
    box-sizing: border-box;
  }
  .food-photo.candy-cake { top: -4px; background: linear-gradient(135deg, #e23b3b, #f2c230, #3aa04a, #2f6fd6, #b545c9); }
  .food-photo.frosted-cake { top: 200px; background: linear-gradient(160deg, #f3f1e6, #dde9a8 55%, #6fb6d9); }
  .food-photo.rainbow-jelly { top: 404px; background: radial-gradient(ellipse at 55% 55%, #d9402e 0%, #e7b43a 25%, #3a9c7c 45%, #3a4fb0 60%, #0c0a08 80%); }
  .platform-mark {
    position: absolute;
    left: 640px;
    top: 320px;
    display: flex;
    align-items: center;
    gap: 10px;
    color: var(--ink);
    font-size: 30px;
  }
  .platform-mark .mark-square {
    width: 26px;
    height: 26px;
    background: var(--ink);
  }
  .platform-rule {
    position: absolute;
    left: 700px;
    top: 362px;
    width: 3px;
    height: 133px;
    background: var(--ink);
  }
  .host-name {
    position: absolute;
    left: 230px;
    top: 410px;
    margin: 0;
    color: var(--ink);
    font-size: 52px;
    line-height: 62px;
  }
  .name-rule {
    position: absolute;
    left: 220px;
    top: 478px;
    width: 483px;
    height: 3px;
    background: var(--ink);
  }
  .channel-name {
    position: absolute;
    left: 300px;
    top: 488px;
    margin: 0;
    color: var(--ink);
    font-size: 26px;
    line-height: 32px;
    letter-spacing: 1px;
  }
  .contact {
    position: absolute;
    left: 230px;
    top: 528px;
    margin: 0;
    color: var(--ink);
    font-size: 20px;
    line-height: 26px;
  }
</style>
</head>
<body>
  <section class="card">
    <div class="slogan-pill"></div>
    <p class="slogan">I'll see you next<br>time, for my<br>next meal</p>
    <div class="channel-logo">Tidy<br>Skillet<br>Show</div>

    <div class="food-photo candy-cake" role="img" aria-label="Photo of a rainbow layer cake covered in colourful candies"></div>
    <div class="food-photo frosted-cake" role="img" aria-label="Photo of a frosted cake with a colourful sliced interior"></div>
    <div class="food-photo rainbow-jelly" role="img" aria-label="Photo of a rainbow layered jelly slice on black"></div>

    <div class="platform-mark"><span class="mark-square"></span>Vidloomer</div>
    <div class="platform-rule"></div>

    <h1 class="host-name">Marcus Delroy</h1>
    <div class="name-rule"></div>
    <p class="channel-name">Tidy Skillet Show</p>
    <p class="contact">www.vidloomer.example/user/TidySkilletShow<br>email - bookings@harrowlanemedia.example</p>
  </section>
</body>
</html>
```